4th Generation Family Business Needs a New Card Design!

We are a family owned 4th Generation company. We are based in the Sydney, Australia area and we are desperately in need of a more modern and classy card. We are monumental masons who design, supply & erect lasting memorials throughout cemeteries in Sydney. Our customers are normally in a period of grieving. I have attached logo files that will need to be implemented on the card. Company was established 1935. Australian Owned and Operated. Card needs to be designed to PIXO.com specification.

Target Market(s)

Our target market is based upon people that a grieving for family members that have passed away. We also deal with alot of companies that own and operate cemeteries.

Industry/Entity Type

Business

Contact Information for Business Card

Simon Harcourt, Operations Manager, 0417293086, simon@harcourtmemorials.com.au
Lewis Harcourt, Director, 0491630572, lewis@harcourtmemorials.com.au
Phone # 02 9561 3048
Website: www.harcourtmemorials.com.au
Address: Suite 17, 8 Palfrey Lane, West Carlow, Sydney NSW 2156

Font styles to use
Serif
Decorative
Script

Requirements
Must have
• Would like to see the logo nicely implemented with a modern design. Embossed lettering would be a nice additive.

```html
<!DOCTYPE html>
<html lang="en">
<head>
<meta charset="utf-8">
<title>Harcourt Memorials – Business Card</title>
<link rel="stylesheet" href="https://fonts.googleapis.com/css2?family=Cinzel:wght@500;600&family=Open+Sans:wght@400;600&display=swap">
<style>
  :root {
    --backdrop: #a7c1ca;
    --card: #1c1c1d;
    --gold: #d9a92b;
    --white: #f2f2f2;
    --shadow: rgba(20, 40, 50, 0.35);
  }
  * { margin: 0; padding: 0; box-sizing: border-box; }
  html, body {
    width: 1200px;
    height: 829px;
    overflow: hidden;
    background: var(--backdrop);
  }
  .sheet {
    position: relative;
    width: 1200px;
    height: 829px;
  }
  .card {
    position: absolute;
    width: 520px;
    height: 316px;
    background: var(--card);
    border-radius: 4px;
    box-shadow: 0 14px 30px var(--shadow);
  }
  .card--front { left: 50px; top: 256px; }
  .card--back  { left: 630px; top: 256px; }

  .brand-name {
    position: absolute;
    font-family: "Open Sans", sans-serif;
    font-weight: 600;
    white-space: nowrap;
    line-height: 1;
  }
  .card--front .brand-name {
    left: 0; right: 0; top: 144px;
    text-align: center;
    font-size: 30px;
    color: var(--gold);
  }
  .card--back .brand-name {
    left: 26px; top: 126px;
    width: 200px;
    text-align: center;
    font-size: 17px;
    color: var(--white);
  }

  .contact {
    position: absolute;
    left: 244px; top: 74px;
    width: 260px;
    font-family: "Open Sans", sans-serif;
    color: var(--white);
    font-size: 12px;
    line-height: 1.5;
  }
  .contact__name {
    font-family: "Cinzel", serif;
    font-weight: 600;
    color: var(--gold);
    font-size: 17px;
    letter-spacing: 0.06em;
  }
  .contact__role {
    font-family: "Cinzel", serif;
    font-weight: 500;
    font-size: 12px;
    letter-spacing: 0.08em;
    margin-bottom: 6px;
  }
  .contact__line { display: flex; align-items: center; gap: 7px; }
  .contact__line svg { width: 11px; height: 11px; flex: none; fill: var(--gold); }
  .contact__address { margin-bottom: 4px; }
</style>
</head>
<body>
<main class="sheet">
  <section class="card card--front" aria-label="Card front">
    <div class="brand-name">Harcourt Memorials</div>
  </section>

  <section class="card card--back" aria-label="Card back">
    <div class="brand-name">Harcourt Memorials</div>
    <div class="contact">
      <div class="contact__name">Simon Harcourt</div>
      <div class="contact__role">OPERATIONS MANAGER</div>
      <div class="contact__address">Suite 17, 8 Palfrey Lane<br>West Carlow, Sydney NSW 2156</div>
      <div class="contact__line">
        <svg viewBox="0 0 12 12" aria-hidden="true"><path d="M2.5 1h2l1 3-1.3 1a6 6 0 0 0 2.8 2.8L8 6.5l3 1v2c0 .8-.7 1.5-1.5 1.5A8.5 8.5 0 0 1 1 2.5C1 1.7 1.7 1 2.5 1z"/></svg>
        <span>02 9561 3048</span>
      </div>
      <div class="contact__line">
        <svg viewBox="0 0 12 12" aria-hidden="true"><rect x="3" y="0.5" width="6" height="11" rx="1"/><rect x="4" y="2" width="4" height="7" fill="#1c1c1d"/></svg>
        <span>0417293086</span>
      </div>
      <div class="contact__line">
        <svg viewBox="0 0 12 12" aria-hidden="true"><rect x="0.5" y="2" width="11" height="8" rx="1"/><path d="M1 3l5 3.5L11 3" stroke="#1c1c1d" stroke-width="1" fill="none"/></svg>
        <span>simon@harcourtmemorials.com.au</span>
      </div>
      <div class="contact__line">
        <svg viewBox="0 0 12 12" aria-hidden="true"><circle cx="6" cy="6" r="5.5"/><path d="M0.5 6h11M6 0.5c-2.5 3-2.5 8 0 11M6 0.5c2.5 3 2.5 8 0 11" stroke="#1c1c1d" stroke-width="0.8" fill="none"/></svg>
        <span>www.harcourtmemorials.com.au</span>
      </div>
    </div>
  </section>
</main>
</body>
</html>
```